Brovanek Data Yellow rose letterhead

I have a new logo for my company but in its current form it is too large to be used on letterhead or as a email signature. I need to have the designer use elements from the current logo and create something close to the original but more suited for smaller items.
Updates

I just uploaded a copy of our logo that does not have the weathered affect. Thanks

Reason: More time for revisions

Industry/Entity Type

It Company

Requirements
Must have
• The design must maintain the visual effect of the current logo. It needs to include the yellow rose and the name of the company.
Nice to have
• It would be nice to maintain the stamp theme and incorporate my name, address, phone, email. etc.

```html
<!DOCTYPE html>
<html lang="en">
<head>
<meta charset="utf-8">
<title>Brovanek Data Letterhead</title>
<link rel="stylesheet" href="https://fonts.googleapis.com/css2?family=Delius&display=swap">
<style>
  :root {
    --paper-light: #ede3cc;
    --paper-mid: #dccfae;
    --paper-edge: #c9b68c;
    --ink-brown: #4d3d34;
    --band-brown: #5c4c42;
    --page: #ffffff;
  }
  html, body {
    margin: 0;
    padding: 0;
    width: 927px;
    height: 1200px;
    overflow: hidden;
    background: var(--page);
  }
  .letterhead {
    position: relative;
    width: 927px;
    height: 1200px;
    background: var(--page);
    font-family: "Delius", "Trebuchet MS", sans-serif;
    color: var(--ink-brown);
  }
  .paper-header {
    position: absolute;
    top: 0;
    left: 0;
    width: 927px;
    height: 210px;
  }
  .brand-mark {
    position: absolute;
    top: 118px;
    right: 32px;
    display: flex;
    align-items: center;
    gap: 10px;
    font-size: 26px;
    color: var(--ink-brown);
  }
  .brand-mark .brand-square {
    width: 18px;
    height: 18px;
    background: var(--ink-brown);
  }
  .sender-details {
    position: absolute;
    top: 446px;
    left: 24px;
    margin: 0;
    padding: 0;
    list-style: none;
    font-size: 14.5px;
    line-height: 27.6px;
  }
  .footer-band {
    position: absolute;
    left: 0;
    bottom: 0;
    width: 927px;
    height: 86px;
    background: var(--band-brown);
  }
</style>
</head>
<body>
<main class="letterhead">
  <svg class="paper-header" viewBox="0 0 927 210" role="img" aria-label="Aged parchment paper strip with a torn lower edge">
    <defs>
      <linearGradient id="parchment" x1="0" y1="0" x2="1" y2="1">
        <stop offset="0" stop-color="#efe6d0"/>
        <stop offset="0.6" stop-color="#e4d8bb"/>
        <stop offset="1" stop-color="#d8c9a5"/>
      </linearGradient>
      <linearGradient id="tearShadow" x1="0" y1="0" x2="0" y2="1">
        <stop offset="0" stop-color="#000" stop-opacity="0.28"/>
        <stop offset="1" stop-color="#000" stop-opacity="0"/>
      </linearGradient>
    </defs>
    <path d="M0 160 L927 160 L927 205 L0 205 Z" fill="url(#tearShadow)"/>
    <path fill="url(#parchment)"
      d="M0 0 H927 V162 L900 165 L870 160 L835 166 L800 161 L760 164 L720 159 L690 163 L640 160 L600 165 L560 160 L520 163 L480 159 L440 164 L400 160 L360 163 L320 159 L280 162 L250 157 L215 162 L180 160 L140 164 L100 159 L60 163 L30 160 L0 164 Z"/>
    <path fill="none" stroke="var(--paper-edge)" stroke-width="2"
      d="M0 164 L30 160 L60 163 L100 159 L140 164 L180 160 L215 162 L250 157 L280 162 L320 159 L360 163 L400 160 L440 164 L480 159 L520 163 L560 160 L600 165 L640 160 L690 163 L720 159 L760 164 L800 161 L835 166 L870 160 L900 165 L927 162"/>
  </svg>

  <div class="brand-mark">
    <span class="brand-square"></span>
    <span class="brand-name">Brovanek Data</span>
  </div>

  <ul class="sender-details">
    <li>Marta Keldane, PhD</li>
    <li>418 NE Sandstone Loop, Ste 2117</li>
    <li>Pell Ridge, TX 76512</li>
    <li>marta@brovanek-data.com</li>
    <li>1-800-555-0147</li>
  </ul>

  <div class="footer-band"></div>
</main>
</body>
</html>
```